Frozen Yogurt "Now Open" Postcard

I would like to see a very fun, vibrant postcard design that will catch people's attention when going through their mail. It will be an announcement that the store is "Now Open". Please refer to the website... www.tundracups.com for details and design inspiration. Include the phone, address (with mini map), and website info.

Use Jumbo Postcard size... 11" x 6"

Target Market(s)

Women, kids and families

Industry/Entity Type

Food Store

Colors
0692cd
e34298
b768aa

Requirements
Must have
• Phone, Web address, mailing address (with map). Vibrant colors, delicious looking frozen yogurt.

```html
<!DOCTYPE html>
<html lang="en">
<head>
<meta charset="utf-8">
<title>Tundra Cups – Now Open Postcard</title>
<link rel="stylesheet" href="https://fonts.googleapis.com/css2?family=Bangers&family=Cabin:wght@400;600;700&display=swap">
<style>
  :root {
    --stage: #1c1c1c;
    --paper: #ffffff;
    --berry: #d02f7a;
    --pink: #e34298;
    --plum: #9a4ea6;
    --orchid: #b768aa;
    --teal: #3fb0b0;
    --mint: #8fcfb8;
    --blue: #0692cd;
    --crimson: #9c1030;
    --ink-line: #b9b9b9;
    --body-font: "Cabin", sans-serif;
  }
  * { box-sizing: border-box; margin: 0; padding: 0; }
  html, body { width: 1200px; height: 900px; overflow: hidden; }
  body { background: var(--stage); position: relative; font-family: var(--body-font); }

  .postcard {
    position: absolute; left: 258px; width: 686px; height: 392px;
    background: var(--paper); overflow: hidden;
  }
  .postcard--front { top: 39px; background: linear-gradient(120deg, #f1e7ee 0%, #ebe6ef 45%, #f3efd9 100%); }
  .postcard--back { top: 468px; }

  /* front */
  .hero-photo {
    position: absolute; left: 0; top: 0; width: 320px; height: 330px;
    background: linear-gradient(150deg, #c9a48e 0%, #b86f62 45%, #d8c7c9 100%);
  }
  .front-wave { position: absolute; left: 0; top: 0; width: 686px; height: 392px; }
  .brand-mark { position: absolute; left: 252px; top: 100px; width: 280px; text-align: center; }
  .brand-mark__name { font-family: var(--body-font); font-weight: 700; font-size: 46px; color: var(--pink); line-height: 1; }
  .brand-mark__tag { font-weight: 600; font-size: 15px; color: var(--teal); letter-spacing: 0.5px; margin-top: 8px; }
  .now-open {
    position: absolute; left: 326px; top: 262px;
    font-family: "Bangers", sans-serif; font-size: 48px; color: var(--crimson);
    letter-spacing: 1px; transform: rotate(-3deg);
  }

  /* back */
  .contact-list { position: absolute; left: 17px; top: 46px; list-style: none; }
  .contact-list li { display: flex; align-items: center; height: 36px; font-weight: 600; font-size: 14.5px; color: var(--plum); }
  .contact-list svg { width: 19px; height: 19px; margin-right: 10px; }
  .back-brand { position: absolute; left: 198px; top: 84px; width: 135px; text-align: center; }
  .back-brand__name { font-weight: 700; font-size: 24px; color: var(--pink); line-height: 1; }
  .back-brand__tag { font-size: 8px; color: var(--teal); margin-top: 4px; letter-spacing: 0.3px; }
  .social-dots { position: absolute; left: 124px; top: 167px; display: flex; gap: 13px; }
  .social-dots span { width: 20px; height: 20px; border-radius: 50%; background: var(--plum); }
  .froyo-photo {
    position: absolute; left: 6px; top: 196px; width: 168px; height: 192px;
    background: radial-gradient(ellipse at 50% 40%, #f59ab4 0%, #f4b8c8 45%, #f4f1f1 80%);
  }
  .location { position: absolute; left: 185px; top: 202px; color: var(--plum); }
  .location__title { font-weight: 600; font-size: 14px; }
  .location__map { width: 129px; height: 81px; margin-top: 6px; background: linear-gradient(135deg, #e7e9ec, #d8dde2); }
  .location__address { font-weight: 600; font-size: 12.5px; line-height: 16px; margin-top: 10px; }
  .divider { position: absolute; left: 342px; top: 40px; width: 1px; height: 312px; background: #9a9a9a; }
  .stamp-box { position: absolute; left: 565px; top: 40px; width: 80px; height: 91px; border: 1px solid #8a8a8a; }
  .address-lines { position: absolute; left: 406px; top: 232px; width: 238px; }
  .address-lines span { display: block; height: 1px; background: var(--ink-line); margin-bottom: 31px; }
</style>
</head>
<body>

<section class="postcard postcard--front">
  <div class="hero-photo" role="img" aria-label="Photo of a smiling young woman eating a cup of frozen yogurt with sprinkles"></div>
  <svg class="front-wave" viewBox="0 0 686 392" aria-hidden="true">
    <defs>
      <linearGradient id="band" x1="0" x2="1">
        <stop offset="0" stop-color="#d52f76"/>
        <stop offset="0.6" stop-color="#c25394"/>
        <stop offset="1" stop-color="#9a5ba9"/>
      </linearGradient>
      <linearGradient id="ribbon" x1="0" x2="1">
        <stop offset="0" stop-color="#1f9fb3"/>
        <stop offset="1" stop-color="#8fcfb8"/>
      </linearGradient>
    </defs>
    <path d="M0 300 C90 265 200 272 300 310 C390 345 440 385 530 370 C610 356 660 300 686 250 L686 392 L0 392 Z" fill="url(#band)"/>
    <path d="M0 300 C90 265 200 272 300 310 C390 345 440 385 530 370 C610 356 660 300 686 250" fill="none" stroke="url(#ribbon)" stroke-width="9"/>
  </svg>
  <div class="brand-mark">
    <div class="brand-mark__name">Tundra Cups</div>
    <div class="brand-mark__tag">FROZEN YOGURT</div>
  </div>
  <div class="now-open">NOW OPEN!</div>
</section>

<section class="postcard postcard--back">
  <ul class="contact-list">
    <li>
      <svg viewBox="0 0 20 20" aria-hidden="true"><circle cx="10" cy="10" r="10" fill="var(--plum)"/><path d="M7 5.5l1.6 2.2-1 1.2c.6 1.3 1.6 2.3 2.8 2.9l1.2-1 2.2 1.5-.8 1.8c-3.6-.3-6.6-3.3-6.9-6.9z" fill="#fff"/></svg>
      925.555.0148
    </li>
    <li>
      <svg viewBox="0 0 20 20" aria-hidden="true"><circle cx="10" cy="10" r="10" fill="var(--plum)"/><rect x="5" y="6.5" width="10" height="7" rx="1" fill="#fff"/><path d="M5.5 7l4.5 3.5L14.5 7" fill="none" stroke="var(--plum)" stroke-width="1.2"/></svg>
      info@tundracups.com
    </li>
    <li>
      <svg viewBox="0 0 20 20" aria-hidden="true"><circle cx="10" cy="10" r="10" fill="var(--plum)"/><g fill="none" stroke="#fff" stroke-width="1.1"><circle cx="10" cy="10" r="5"/><ellipse cx="10" cy="10" rx="2.2" ry="5"/><path d="M5 10h10"/></g></svg>
      tundracups.com
    </li>
  </ul>
  <div class="back-brand">
    <div class="back-brand__name">Tundra Cups</div>
    <div class="back-brand__tag">FROZEN YOGURT</div>
  </div>
  <div class="social-dots" aria-hidden="true"><span></span><span></span><span></span></div>
  <div class="froyo-photo" role="img" aria-label="Photo of strawberry frozen yogurt swirl in a white bowl with fresh strawberries and mint"></div>
  <div class="location">
    <div class="location__title">Location :</div>
    <div class="location__map" role="img" aria-label="Mini street map showing the store location"></div>
    <div class="location__address">Willowbrook Plaza<br>1820 Cedar Run Way<br>Brightwater, CA<br>90210</div>
  </div>
  <div class="divider"></div>
  <div class="stamp-box"></div>
  <div class="address-lines"><span></span><span></span><span></span><span></span></div>
</section>

</body>
</html>
```